KBT Business Cards

We require business cards for our business. We would like a matte black back to the card, with our logo centred in the middle. The front side of the card is open to design.

Target Market(s)

Clients looking for legal services (professional)

Industry/Entity Type

Legal

Contact Information for Business Card

Doran Kelbrath
Partner
Mobile: 0461 738 524
Email: doran@kbtlaw.co
Website: www.kbtlaw.co
Level 3, 118 Wendmore Street
Sydney NSW 2000

Font styles to use
Other font styles liked:
• Avenir

Colors
f04a50
ffffff
1b1b1b

Requirements
Must have
• Black back with logo included in the centre of the card.
• Our font is Avenir.

```html
<!DOCTYPE html>
<html lang="en">
<head>
<meta charset="utf-8">
<title>KBT Legal – Business Cards</title>
<link href="https://fonts.googleapis.com/css2?family=Nunito+Sans:wght@400;600;700;800&display=swap" rel="stylesheet">
<style>
  :root {
    --brand-red: #d21f4a;
    --brand-red-deep: #a8173a;
    --ink: #1b1b1b;
    --card-black: #161616;
    --paper: #ffffff;
    --stage: #232323;
    --muted-ink: #2a2a2a;
  }
  * { box-sizing: border-box; margin: 0; padding: 0; }
  html, body { width: 1200px; height: 960px; overflow: hidden; }
  body {
    background: var(--stage);
    font-family: "Nunito Sans", "Avenir", sans-serif;
    position: relative;
  }
  .card {
    position: absolute;
    width: 540px;
    height: 330px;
    border-radius: 6px;
    overflow: hidden;
    box-shadow: 0 18px 40px rgba(0,0,0,0.45);
  }

  /* Back of card */
  .card-back {
    left: 600px;
    top: 110px;
    background: radial-gradient(ellipse at 40% 30%, #262626 0%, var(--card-black) 70%);
  }
  .back-mark {
    position: absolute;
    left: 0; right: 0; top: 120px;
    display: flex;
    justify-content: center;
    align-items: center;
    gap: 16px;
  }
  .mark-square {
    width: 34px; height: 34px;
    background: var(--brand-red);
  }
  .back-mark .firm-name {
    color: var(--paper);
    font-weight: 800;
    font-size: 46px;
    letter-spacing: 2px;
    line-height: 1;
  }
  .back-web {
    position: absolute;
    left: 0; right: 0; bottom: 58px;
    text-align: center;
    color: var(--paper);
    font-size: 15px;
    letter-spacing: 4px;
  }
  .back-web .accent { color: var(--brand-red); font-weight: 700; }

  /* Front of card */
  .card-front {
    left: 110px;
    top: 480px;
    background: var(--paper);
  }
  .front-art { position: absolute; inset: 0; width: 100%; height: 100%; }
  .front-mark {
    position: absolute;
    left: 40px; top: 44px;
    display: flex;
    align-items: center;
    gap: 12px;
  }
  .front-mark .mark-square { width: 26px; height: 26px; }
  .front-mark .firm-name {
    color: var(--ink);
    font-weight: 800;
    font-size: 34px;
    letter-spacing: 1.5px;
    line-height: 1;
  }
  .address {
    position: absolute;
    left: 40px; top: 108px;
    color: var(--muted-ink);
    font-size: 13.5px;
    line-height: 1.45;
  }
  .holder {
    position: absolute;
    right: 40px; top: 108px;
    text-align: right;
  }
  .holder-name {
    color: var(--brand-red);
    font-weight: 800;
    font-size: 19px;
    letter-spacing: 0.5px;
  }
  .holder-role {
    color: var(--muted-ink);
    font-size: 13px;
    letter-spacing: 0.5px;
    margin-top: 2px;
  }
  .contacts {
    position: absolute;
    right: 34px; bottom: 20px;
    list-style: none;
    color: var(--paper);
    font-size: 14px;
    line-height: 1;
  }
  .contacts li {
    display: flex;
    justify-content: flex-end;
    align-items: center;
    gap: 9px;
    margin-top: 8px;
  }
  .contacts svg { width: 14px; height: 14px; flex: none; }
</style>
</head>
<body>

  <section class="card card-back" aria-label="Card back">
    <div class="back-mark">
      <span class="mark-square"></span>
      <span class="firm-name">KBT LEGAL</span>
    </div>
    <p class="back-web">www.<span class="accent">kbtlaw</span>.co</p>
  </section>

  <section class="card card-front" aria-label="Card front">
    <svg class="front-art" viewBox="0 0 540 330" preserveAspectRatio="none" aria-hidden="true">
      <defs>
        <linearGradient id="red-band" x1="0" x2="1" y1="0" y2="0">
          <stop offset="0" stop-color="#e0355e"/>
          <stop offset="1" stop-color="#9e1434"/>
        </linearGradient>
      </defs>
      <path d="M0,170 C160,158 330,200 540,164" fill="none" stroke="url(#red-band)" stroke-width="2"/>
      <path d="M0,184 C160,174 330,214 540,178 L540,192 C330,228 160,190 0,202 Z" fill="url(#red-band)"/>
      <path d="M0,202 C160,190 330,228 540,192 L540,330 L0,330 Z" fill="#111"/>
    </svg>

    <div class="front-mark">
      <span class="mark-square"></span>
      <span class="firm-name">KBT LEGAL</span>
    </div>

    <p class="address">Level 3, 118 Wendmore Street<br>Sydney NSW 2000</p>

    <div class="holder">
      <p class="holder-name">DORAN KELBRATH</p>
      <p class="holder-role">PARTNER</p>
    </div>

    <ul class="contacts">
      <li>0461 738 524
        <svg viewBox="0 0 14 14" aria-label="Mobile"><rect x="1" y="1" width="12" height="12" rx="3" fill="none" stroke="#fff" stroke-width="1.2"/><rect x="5" y="3.5" width="4" height="7" rx="0.8" fill="none" stroke="#fff" stroke-width="1"/></svg>
      </li>
      <li>doran@kbtlaw.co
        <svg viewBox="0 0 14 14" aria-label="Email"><rect x="1" y="3" width="12" height="8" fill="none" stroke="#fff" stroke-width="1.2"/><path d="M1,3 L7,8 L13,3" fill="none" stroke="#fff" stroke-width="1.2"/></svg>
      </li>
      <li>www.kbtlaw.co
        <svg viewBox="0 0 14 14" aria-label="Website"><circle cx="7" cy="7" r="5.8" fill="none" stroke="#fff" stroke-width="1.2"/><ellipse cx="7" cy="7" rx="2.6" ry="5.8" fill="none" stroke="#fff" stroke-width="1"/><path d="M1.2,7 H12.8 M2,4 H12 M2,10 H12" stroke="#fff" stroke-width="0.9"/></svg>
      </li>
    </ul>
  </section>

</body>
</html>
```